UK Online Auction Site needs a clever design

We need a contemporary landing page and registration page design for a UK auction website, that look equally at home on PC's and tablets . The design should be fresh, bright, clean, professional, robust, and familiar. We would like to see something clever but functional.

Online

```html
<!DOCTYPE html>
<html lang="en">
<head>
<meta charset="utf-8">
<title>Bidwell – UK Online Auctions</title>
<link rel="stylesheet" href="https://fonts.googleapis.com/css2?family=Lato:wght@300;400;700&display=swap">
<style>
:root{
  --blue:#0a7cc9;
  --blue-dark:#0868ad;
  --orange:#f26a1b;
  --text:#333;
  --muted:#8a8a8a;
  --panel:#ececec;
  --panel-light:#f6f6f6;
  --border:#dedede;
  --footer:#151515;
  --footer-text:#9a9a9a;
}
*{box-sizing:border-box;margin:0;padding:0}
html,body{width:766px;height:1200px;overflow:hidden}
body{position:relative;font-family:'Lato',sans-serif;color:var(--text);background:#fff;font-size:10px}
a{color:inherit;text-decoration:none}
.abs{position:absolute}

.topbar{left:0;top:0;width:766px;height:18px;background:var(--blue);color:#fff;font-size:8px;text-align:right;padding:4px 63px 0 0}
.topbar span{margin:0 4px}
.header{left:0;top:18px;width:766px;height:78px;background:linear-gradient(#fafafa,#e9e9e9);border-bottom:1px solid #e2e2e2}
.brand{left:63px;top:32px;display:flex;align-items:center;gap:8px;color:var(--blue);font-weight:700;font-size:30px;letter-spacing:-.5px}
.brand-dot{width:14px;height:14px;border-radius:50%;background:var(--blue)}
.search{left:389px;top:42px;width:314px;height:36px;display:flex;box-shadow:0 1px 3px rgba(0,0,0,.08)}
.search-field{flex:1;background:#fff;color:#aaa;font-size:8px;padding:13px 0 0 11px}
.search-btn{width:30px;background:var(--blue);display:flex;align-items:center;justify-content:center;border-radius:0 3px 3px 0}

.sidebar{left:63px;top:113px;width:207px;height:243px;background:var(--panel)}
.sidebar-title{height:30px;background:var(--blue);color:#fff;font-weight:700;font-size:11px;padding:8px 0 0 17px}
.sidebar ul{list-style:none;padding:5px 0 0 19px}
.sidebar li{height:20px;font-size:9px;color:#555;line-height:20px}
.sidebar li::before{content:"→";color:#222;margin-right:6px}

.nav{left:283px;top:113px;width:419px;height:32px;background:var(--blue);display:flex;border-radius:2px}
.nav a{color:#fff;font-size:9.5px;padding:10px 16px 0;border-right:1px solid rgba(255,255,255,.25)}
.nav a:last-child{border-right:none}

.hero{left:283px;top:157px;width:419px;height:199px;background:#fff;border:1px solid #eee}
.hero-offer{left:26px;top:36px;color:var(--orange);font-weight:300;font-size:31px}
.hero-sub{left:26px;top:70px;font-weight:300;font-size:19px;color:#222}
.hero-title{left:26px;top:96px;color:var(--orange);font-weight:300;font-size:32px}
.hero-btn{left:50px;top:149px;width:69px;height:25px;background:var(--blue);color:#fff;font-weight:700;font-size:9px;text-align:center;line-height:25px;border-radius:2px}
.hero-img{left:178px;top:82px;width:237px;height:116px;background:radial-gradient(ellipse at 40% 55%,#3a3a3a,#1a1a1a 55%,#e6e6e6 75%,#fff);border-radius:4px}
.hero-next{left:387px;top:78px;width:20px;height:20px;border-radius:50%;background:#eee;border:1px solid #ccc;display:flex;align-items:center;justify-content:center}

.info{top:378px;width:207px;height:131px;background:linear-gradient(#f4f4f4,#e7e7e7)}
.info h2{position:absolute;left:19px;top:35px;font-weight:300;font-size:17px;color:var(--blue)}
.info p{position:absolute;left:19px;top:70px;width:140px;font-size:9px;line-height:16px;color:#222}
.info svg{position:absolute}

.section-bar{left:63px;width:639px;height:39px;background:var(--blue);color:#fff;font-weight:700;font-size:10.5px;padding:14px 0 0 13px}
.section-bar::after{content:"";position:absolute;left:30px;right:30px;bottom:-10px;height:10px;background:radial-gradient(ellipse at 50% 0,rgba(0,0,0,.35),transparent 70%)}

.card{width:154px;height:166px;background:var(--panel);border:1px solid var(--border)}
.card-img{height:104px;background:#fff;display:flex;align-items:center;justify-content:center}
.card-img div{width:80px;height:62px;border-radius:6px}
.card-name{padding:7px 0 0 9px;font-size:9px;line-height:16px;color:var(--muted);width:150px}
.card-price{padding:4px 0 0 9px;font-size:8.5px;font-weight:700;color:var(--blue)}

.footer{left:0;top:1018px;width:766px;height:182px;background:var(--footer);color:var(--footer-text)}
.fcol{top:31px}
.fcol h3{font-weight:400;font-size:11px;color:#fff;margin-bottom:5px}
.fcol li{list-style:none;font-size:8.5px;line-height:20px}
.social{display:flex;align-items:center;gap:6px}
.social i{display:inline-block;width:9px;height:9px}
.copyright{left:0;top:159px;width:766px;text-align:center;color:#fff;font-size:8.5px}
</style>
</head>
<body>

<div class="abs topbar"><a>Sign In</a><span>|</span><a>Register</a></div>

<header class="abs header"></header>
<div class="abs brand"><span class="brand-dot"></span>Bidwell</div>
<div class="abs search">
  <div class="search-field">Search Your Keyword</div>
  <div class="search-btn"><svg width="11" height="11" viewBox="0 0 12 12"><circle cx="5" cy="5" r="3.6" fill="none" stroke="#fff" stroke-width="1.8"/><line x1="7.6" y1="7.6" x2="11" y2="11" stroke="#fff" stroke-width="2"/></svg></div>
</div>

<aside class="abs sidebar">
  <div class="sidebar-title">Shop by category</div>
  <ul>
    <li>All categories</li><li>Automotive</li><li>Business &amp; Industrial</li>
    <li>Clothing and Accessories</li><li>Digital Products</li><li>Electronics</li>
    <li>Mobile &amp; Accessories</li><li>Televisions</li><li>Computers and Gadgets</li>
    <li>All categories</li>
  </ul>
</aside>

<nav class="abs nav"><a>Sell</a><a>Sign In</a><a>Cart</a><a>Favourite</a><a>Help</a></nav>

<section class="abs hero">
  <div class="abs hero-offer">40% Offer</div>
  <div class="abs hero-sub">The Smartest</div>
  <div class="abs hero-title">Cameras</div>
  <a class="abs hero-btn">Shop Now</a>
  <div class="abs hero-img" role="img" aria-label="Black compact camera beside a touchscreen camera back"></div>
  <div class="abs hero-next"><svg width="8" height="8" viewBox="0 0 8 8"><path d="M2.5 1l3 3-3 3" fill="none" stroke="#999" stroke-width="1.5"/></svg></div>
</section>

<div class="abs info" style="left:63px">
  <h2>Welcome</h2>
  <p>Even if you're new or already experienced,</p>
  <svg style="left:155px;top:78px" width="40" height="40" viewBox="0 0 40 40" fill="#c9c9c9"><path d="M4 2h32l4 10H0z"/><rect x="4" y="14" width="32" height="4"/><rect x="6" y="20" width="28" height="18" fill="none" stroke="#c9c9c9" stroke-width="3"/><rect x="4" y="36" width="32" height="3"/></svg>
</div>
<div class="abs info" style="left:279px">
  <h2 style="top:32px">Sign in</h2>
  <p>Sign-in to your account in order to buy, sell or manage your preferences.</p>
  <svg style="left:155px;top:82px" width="43" height="44" viewBox="0 0 43 44" fill="#c9c9c9"><path d="M22 0h20v40l-20 4z"/><path d="M0 16h12v-6l10 10-10 10v-6H0z"/></svg>
</div>
<div class="abs info" style="left:494px">
  <h2 style="top:34px">Shop with confidence</h2>
  <p style="top:67px;width:150px">Completely safe, Premium sellers, Feedback rating system</p>
  <svg style="left:161px;top:73px" width="36" height="46" viewBox="0 0 36 46" fill="#c9c9c9"><circle cx="18" cy="5" r="5"/><path d="M12 12h12l6 16h-6l-2 18h-5l-2-12-6 12H4l6-16z"/></svg>
</div>

<div class="abs section-bar" style="top:531px">Featured</div>
<div class="abs section-bar" style="top:778px">Items from seller stores</div>

<div class="abs card" style="left:63px;top:586px"><div class="card-img"><div role="img" aria-label="Red compact digital camera" style="background:radial-gradient(#9a9a9a 20%,#a3162b 45%)"></div></div><div class="card-name">NEW IN BOX! Nimbus Slate Tablet</div><div class="card-price">US $2,500.00</div></div>
<div class="abs card" style="left:225px;top:586px"><div class="card-img"><div role="img" aria-label="Smartphone with red earphones" style="width:50px;background:linear-gradient(#2a2a2a,#5a1010)"></div></div><div class="card-name">NEW IN BOX! Nimbus Slate Tablet</div><div class="card-price">US $2,500.00</div></div>
<div class="abs card" style="left:387px;top:586px"><div class="card-img"><div role="img" aria-label="Steel wristwatch with black dial" style="width:50px;height:96px;background:radial-gradient(circle,#222 30%,#b8b8b8 45%,#e0e0e0)"></div></div><div class="card-name">NEW IN BOX! Nimbus Slate Tablet</div><div class="card-price">US $2,500.00</div></div>
<div class="abs card" style="left:549px;top:586px"><div class="card-img"><div role="img" aria-label="Silver charm bracelet with heart pendant" style="background:radial-gradient(circle,#fff 45%,#c7c7c7 55%,#fff 70%)"></div></div><div class="card-name">NEW IN BOX! Nimbus Slate Tablet</div><div class="card-price">US $2,500.00</div></div>

<div class="abs card" style="left:63px;top:834px"><div class="card-img"><div role="img" aria-label="Diamond eternity ring" style="height:40px;background:linear-gradient(#f4f4f4,#d9c48a)"></div></div><div class="card-name">NEW IN BOX! Nimbus Slate Tablet</div><div class="card-price">US $2,500.00</div></div>
<div class="abs card" style="left:225px;top:834px"><div class="card-img"><div role="img" aria-label="Sunglasses with orange lenses" style="height:36px;background:linear-gradient(90deg,#e8541d,#f2a03c,#2e5c9a,#f2a03c,#e8541d)"></div></div><div class="card-name">NEW IN BOX! Nimbus Slate Tablet</div><div class="card-price">US $2,500.00</div></div>
<div class="abs card" style="left:387px;top:834px"><div class="card-img"><div role="img" aria-label="Black leather handbag" style="background:linear-gradient(#333,#0e0e0e)"></div></div><div class="card-name">NEW IN BOX! Nimbus Slate Tablet</div><div class="card-price">US $2,500.00</div></div>
<div class="abs card" style="left:549px;top:834px"><div class="card-img"><div role="img" aria-label="Black smartphone showing a screen" style="width:42px;height:80px;background:linear-gradient(#111,#3b6fb0 30%,#e8eef6 50%,#111 85%)"></div></div><div class="card-name">NEW IN BOX! Nimbus Slate Tablet</div><div class="card-price">US $2,500.00</div></div>

<footer class="abs footer">
  <div class="abs fcol" style="left:63px"><h3>bidwell.co.uk</h3><ul><li>Advertising</li><li>Knowledge Base</li><li>Forum</li><li>Stores</li><li>Want Ads</li></ul></div>
  <div class="abs fcol" style="left:191px"><h3>Buy</h3><ul><li>Categories</li><li>Search</li><li>Currency Converter</li></ul></div>
  <div class="abs fcol" style="left:317px"><h3>Sell</h3><ul><li>Sell New Item</li><li>Sell Bulk Items</li></ul></div>
  <div class="abs fcol" style="left:430px"><h3>Support</h3><ul><li>Contact</li><li>Terms</li><li>Privacy</li><li>RSS</li></ul></div>
  <div class="abs fcol" style="left:527px"><h3>Others</h3><ul><li>About</li><li>News</li><li>Feeds</li></ul></div>
  <div class="abs fcol" style="left:622px"><h3>Stay Connected</h3><ul>
    <li class="social"><i style="background:#3b5a99"></i>Circlenet</li>
    <li class="social"><i style="background:#2aa3d8"></i>Chirpline</li>
    <li class="social"><i style="background:#d23b2a"></i>Plusroom</li>
  </ul></div>
  <div class="abs copyright">Copyright ©2014, bidwell.co.uk</div>
</footer>

</body>
</html>
```